RevelHubQZ Business Cards

Front
Has logo with a design. Website address (www.revelhubqz-example.net)
Has slogan (discover the nightlife)
Has phone number (5182297734)
Should be bold and stands out.

Back
Has details about what we offer.

Events
Search upcoming events
Submit events
Party Image Gallery
View and download HQ party images
Sign up as a contributing event photographer and get paid!
Tickets
Sell your event tickets online for free!
Direct pay
No ticket fee

Target Market(s)

These cards will be handed out in clubs and events to patrons.

Industry/Entity Type

Business

Contact Information for Business Card

Should match or mirror our website in some sort of way. Visit the website to get ideas.

Requirements
Must have
• Must be designed for a 3x3 inch card.

```html
<!DOCTYPE html>
<html lang="en">
<head>
<meta charset="utf-8">
<title>RevelHubQZ Business Cards</title>
<link rel="stylesheet" href="https://fonts.googleapis.com/css2?family=Questrial&family=Didact+Gothic&display=swap">
<style>
  :root {
    --backdrop: #e0e0de;
    --card: #fafafa;
    --brand-blue: #00a9e4;
    --brand-pink: #e2357f;
    --ink: #2a2a2a;
    --muted: #555555;
    --white: #ffffff;
  }
  * { box-sizing: border-box; margin: 0; padding: 0; }
  html, body {
    width: 1200px; height: 659px; overflow: hidden;
    background: var(--backdrop);
    font-family: "Questrial", "Didact Gothic", sans-serif;
  }
  .card {
    position: absolute; top: 142px;
    width: 374px; height: 374px;
    background: var(--card);
    overflow: hidden;
  }
  .card--front { left: 201px; }
  .card--back { left: 624px; }

  .brand-mark {
    position: absolute; left: 162px; top: 40px;
    width: 50px; height: 50px; border-radius: 50%;
    background: var(--brand-blue);
  }
  .brand-name {
    position: absolute; left: 0; right: 0; top: 110px;
    text-align: center; font-size: 27px; color: var(--brand-blue);
  }
  .brand-slogan {
    position: absolute; left: 0; right: 0; top: 147px;
    text-align: center; font-size: 9px; letter-spacing: 4.5px;
    color: var(--ink);
  }

  .name-band {
    position: absolute; left: 0; right: 0; top: 189px; height: 60px;
    background: var(--brand-blue); color: var(--white); text-align: center;
  }
  .person-name { margin-top: 9px; font-size: 21px; font-weight: 700; font-family: "Didact Gothic", sans-serif; letter-spacing: 0.3px; }
  .person-title { font-size: 12px; margin-top: 1px; opacity: 0.9; }

  .contact {
    position: absolute; left: 0; right: 0; top: 267px;
    list-style: none; text-align: center;
    font-size: 14.5px; line-height: 17px; color: var(--ink);
  }

  .offer-band {
    position: absolute; left: 0; right: 0; top: 38px; height: 30px;
    background: var(--brand-blue); color: var(--white);
    text-align: center; font-size: 16px; font-weight: 700;
    font-family: "Didact Gothic", sans-serif; line-height: 30px; letter-spacing: 0.5px;
  }
  .offer-list {
    position: absolute; left: 0; right: 0; top: 86px;
    list-style: none; text-align: center;
    font-size: 14px; line-height: 21.5px; color: var(--ink);
  }

  .equalizer-strip {
    position: absolute; left: 0; right: 0; bottom: 0; height: 32px;
    background: linear-gradient(to bottom, #e888b3 0%, #e888b3 35%, #7fd2f0 35%, var(--brand-blue) 100%);
  }
</style>
</head>
<body>
  <section class="card card--front">
    <div class="brand-mark"></div>
    <div class="brand-name">RevelHubQZ</div>
    <div class="brand-slogan">discover the nightlife</div>
    <div class="name-band">
      <div class="person-name">Dana Morel</div>
      <div class="person-title">Managing Director</div>
    </div>
    <ul class="contact">
      <li>5182297734</li>
      <li>support@revelhubqz-example.net</li>
      <li>www.revelhubqz-example.net</li>
    </ul>
    <div class="equalizer-strip" role="img" aria-label="Decorative pink and blue equalizer bar pattern"></div>
  </section>

  <section class="card card--back">
    <div class="offer-band">WE OFFER</div>
    <ul class="offer-list">
      <li>Events</li>
      <li>Search upcoming events</li>
      <li>Submit events</li>
      <li>Party Image Gallery</li>
      <li>View and download HQ party images</li>
      <li>Sign up as a contributing event</li>
      <li>photographer and get paid!</li>
      <li>Tickets</li>
      <li>Sell your event tickets online for free!</li>
      <li>Direct pay</li>
      <li>No ticket fee</li>
    </ul>
    <div class="equalizer-strip" role="img" aria-label="Decorative pink and blue equalizer bar pattern"></div>
  </section>
</body>
</html>
```